Verdant Ledger - Paid Surveys publisher portal

• Homepage
• Blank Sub Page (Where content goes in between the header/footer)
• Publisher Application Page, complete with Form
• Survey Wall page

Sites that are in a similar vertical that have interesting designs:
rovabin.com
quillmarsh.com
dovek.com
tarn.io

This is a business-to-business site, and needs to have this type of feel to it. Focus on generating revenue, offer completion, paid surveys is the market.

Format: HTML/CSS

Link to current version of application, and form:
https://gridwaveform.brokelqest.com
https://gridwaveform.brokelqest.com/apply
https://gridwaveform.brokelqest.com/panel/4/morvath_user

Please note that we are changing the brand of this project, the name will be determined shortly but everything else remains. It will likely be Verdant Ledger instead of GridWaveform. We will confirm.

Industry/Entity Type

Market Research

Coding

Coded - Design and coding required

Number of Pages Required

4 page

Font styles to use
Sans Serif

Colors

Designer to choose colors to be used in the design.

```html
<!DOCTYPE html>
<html lang="en">
<head>
<meta charset="utf-8">
<title>Survey · Verdant Ledger</title>
<link rel="stylesheet" href="https://fonts.googleapis.com/css2?family=Roboto:wght@300;400;500;700&family=Roboto+Condensed:wght@400;700&display=swap">
<style>
  :root {
    --header-bg: #0b0b0b;
    --hero-bg: #3a3a3c;
    --hero-overlay: rgba(20,20,22,0.55);
    --page-bg: #ffffff;
    --ink: #1d1d1d;
    --ink-soft: #2b2b2b;
    --brand-blue: #1f3e8f;
    --brand-blue-dark: #15307a;
    --nav-text: #ffffff;
    --footer-bg: #262626;
    --footer-text: #8c8c8c;
    --checkbox-border: #6d6d6d;
  }
  * { box-sizing: border-box; margin: 0; padding: 0; }
  html, body { width: 1200px; height: 1091px; overflow: hidden; background: var(--page-bg); }
  body { position: relative; font-family: "Roboto", Arial, sans-serif; color: var(--ink); }

  .site-header { position: absolute; left: 0; top: 0; width: 1200px; height: 86px; background: var(--header-bg); }
  .brand { position: absolute; left: 181px; top: 16px; display: flex; align-items: center; gap: 10px; }
  .brand-mark { width: 52px; height: 52px; border-radius: 50%; background: var(--brand-blue); }
  .brand-name { font-family: "Roboto Condensed", Arial, sans-serif; font-weight: 700; font-size: 21px; color: #ffffff; line-height: 1; }
  .main-nav { position: absolute; top: 0; left: 465px; height: 86px; display: flex; gap: 0; }
  .nav-item { position: relative; height: 86px; display: flex; align-items: center; font-family: "Roboto Condensed", Arial, sans-serif; font-weight: 700; font-size: 13.5px; color: var(--nav-text); letter-spacing: 0.2px; }
  .nav-item.home { width: 71px; }
  .nav-item.publisher { width: 167px; }
  .nav-item.survey { width: 60px; }
  .nav-item.survey::after { content: ""; position: absolute; left: 0; bottom: 2px; width: 47px; height: 3px; background: #ffffff; }
  .nav-item svg { margin-left: 5px; }
  .account-link { position: absolute; left: 884px; top: 31px; display: flex; align-items: center; gap: 8px; font-family: "Roboto Condensed", Arial, sans-serif; font-size: 13.5px; color: #ffffff; }
  .search-icon { position: absolute; left: 1014px; top: 33px; }

  .page-hero { position: absolute; left: 0; top: 86px; width: 1200px; height: 188px; background: linear-gradient(90deg, #5a5a5c 0%, #4a4b4f 30%, #5f6064 60%, #48494b 100%); }
  .page-hero .hero-photo { position: absolute; inset: 0; background: var(--hero-overlay); }
  .page-hero h1 { position: absolute; left: 0; width: 1200px; top: 72px; text-align: center; font-weight: 700; font-size: 34px; color: #ffffff; }

  .survey-title { position: absolute; left: 0; width: 1200px; top: 318px; text-align: center; font-weight: 300; font-size: 36px; color: var(--ink); }

  .question { position: absolute; left: 173px; top: 440px; width: 420px; }
  .question-text { display: flex; gap: 14px; font-weight: 700; font-size: 13.5px; color: var(--ink); }
  .options { list-style: none; }
  .option { position: absolute; left: 0; width: 420px; display: flex; gap: 10px; font-size: 14.5px; line-height: 22px; color: var(--ink-soft); }
  .option .box { flex: none; width: 16px; height: 16px; border: 1px solid var(--checkbox-border); margin-top: 5px; }
  .option:nth-child(1) { top: 44px; }
  .option:nth-child(2) { top: 100px; }
  .option:nth-child(3) { top: 153px; }
  .option:nth-child(4) { top: 213px; }

  .survey-photo { position: absolute; left: 689px; top: 432px; width: 338px; height: 277px; background: linear-gradient(135deg, #e8e2d8 0%, #c9ccd2 45%, #6f86a6 70%, #efeeec 100%); }

  .next-button { position: absolute; left: 539px; top: 811px; width: 122px; height: 40px; background: var(--brand-blue-dark); color: #ffffff; font-family: "Roboto Condensed", Arial, sans-serif; font-weight: 700; font-size: 14px; letter-spacing: 0.5px; display: flex; align-items: center; justify-content: center; }

  .site-footer { position: absolute; left: 0; top: 929px; width: 1200px; height: 162px; background: var(--footer-bg); }
  .back-to-top { position: absolute; left: 584px; top: 911px; width: 32px; height: 32px; border-radius: 50%; background: var(--footer-bg); display: flex; align-items: center; justify-content: center; }
  .footer-links { position: absolute; top: 37px; left: 0; width: 1200px; text-align: center; font-size: 12px; color: var(--footer-text); }
  .social { position: absolute; top: 75px; left: 582px; display: flex; gap: 12px; }
  .social span { width: 12px; height: 12px; border-radius: 50%; background: #ffffff; }
  .copyright { position: absolute; top: 117px; left: 0; width: 1200px; text-align: center; font-size: 12px; color: var(--footer-text); }
</style>
</head>
<body>
  <header class="site-header">
    <div class="brand"><span class="brand-mark"></span><span class="brand-name">Verdant Ledger</span></div>
    <nav class="main-nav">
      <span class="nav-item home">HOME<svg width="8" height="6" viewBox="0 0 8 6"><path d="M1 1l3 3 3-3" stroke="#fff" stroke-width="1.5" fill="none"/></svg></span>
      <span class="nav-item publisher">PUBLISHER APPLICATION</span>
      <span class="nav-item survey">SURVEY</span>
    </nav>
    <div class="account-link">
      <svg width="11" height="12" viewBox="0 0 11 12"><circle cx="5.5" cy="3" r="3" fill="#fff"/><path d="M0 12c0-4 2.5-5 5.5-5s5.5 1 5.5 5z" fill="#fff"/></svg>
      <span>Login / Signup</span>
      <svg width="8" height="6" viewBox="0 0 8 6"><path d="M1 1l3 3 3-3" stroke="#fff" stroke-width="1.5" fill="none"/></svg>
    </div>
    <svg class="search-icon" width="14" height="14" viewBox="0 0 14 14"><circle cx="5.5" cy="5.5" r="4.2" stroke="#fff" stroke-width="2" fill="none"/><path d="M8.6 8.6l4 4" stroke="#fff" stroke-width="2.2"/></svg>
  </header>

  <section class="page-hero">
    <div class="hero-photo" role="img" aria-label="Hands holding a tablet showing a line chart"></div>
    <h1>Survey</h1>
  </section>

  <h2 class="survey-title">Aut reiciendis voluptatibus</h2>

  <div class="question">
    <p class="question-text"><span>1.</span><span>Quod maxime placeat facere possimus ?</span></p>
    <ul class="options">
      <li class="option"><span class="box"></span><span>Nemo enim ipsam voluptatem quia voluptas sit aspernatur aut odit aut fugit, sed quia.</span></li>
      <li class="option"><span class="box"></span><span>Nemo enim ipsam voluptatem quia voluptas sit aspernatur aut odit aut fugit, sed quia.</span></li>
      <li class="option"><span class="box"></span><span>Nemo enim ipsam voluptatem quia voluptas sit aspernatur aut odit aut fugit, sed quia.</span></li>
      <li class="option"><span class="box"></span><span>Nemo enim ipsam voluptatem quia voluptas sit aspernatur aut odit aut fugit, sed quia.</span></li>
    </ul>
  </div>

  <div class="survey-photo" role="img" aria-label="Woman with a mug sitting on a sofa using a laptop"></div>

  <div class="next-button">NEXT</div>

  <footer class="site-footer">
    <p class="footer-links">Home | Publisher | Survey</p>
    <div class="social"><span></span><span></span></div>
    <p class="copyright">©Copyright information here</p>
  </footer>
  <div class="back-to-top"><svg width="10" height="7" viewBox="0 0 10 7"><path d="M1 6l4-4 4 4" stroke="#fff" stroke-width="1.6" fill="none"/></svg></div>
</body>
</html>
```